We need 3 A2 posters similar look but different enough to be eye catching when changed.

We are a healthcare centre that requires 3 A2 posters - simple, similar but different background colours. These posters will be used within our business to promote services we provide to our clients.

The design should include our logo(attached), a large header and a large section in the middle of the poster to promote the event. We need a blank text box (which WE can insert text to advertise), and 1 image to advertise the event. Please note, we do not need you to choose an image we simply would like you to place a demo to give us an idea of where it should sit.

We want to use the bubble design (attached) as a background and the company colours pink, orange and blue - as on our website. Attached is a copy of our logo and background bubble effect. You can also refer to our website - www.tallowbrookwellness.com.au for more inspiration.

Just to reiterate, these posters should be simple, different but have a uniform feel. They should have an empty middle section that can be edited to add text and a space for an eye catching title and matching image.

Our services include Chiropractic, Podiatry, Nutrition, Massage, Yoga, Pilates and Specialised rehabilitation classes.

Reason: Hi designers, I know we are all busy but I really need more designs from the designers I invited to this project and look forward to receiving more designs. Any questions please let me know. Regards, Marion

Reason: Hi all Increased the budget Regards Marion

Corporate Sydney City office workers

Healthcare

• logo and company colours
section in the middles that can be edited to add text
Space allocated for image placement
Catchy title/header

```html
<!DOCTYPE html>
<html lang="en">
<head>
<meta charset="utf-8">
<title>Tallowbrook Wellness – Poster</title>
<link rel="stylesheet" href="https://fonts.googleapis.com/css2?family=Mulish:wght@700;800&display=swap">
<style>
  :root {
    --brand-purple: #bb34e2;
    --brand-blue: #5d80f5;
    --brand-orange: #d98f42;
    --bg-lavender: #dcaee8;
    --bg-lavender-deep: #cf95e0;
    --panel-white: #ffffff;
    --text-purple: #b52fe0;
    --stage: #ffffff;
  }
  * { box-sizing: border-box; margin: 0; padding: 0; }
  html, body {
    width: 928px; height: 1200px; overflow: hidden;
    background: var(--stage);
    font-family: "Mulish", "Century Gothic", sans-serif;
  }
  .canvas { position: relative; width: 928px; height: 1200px; }

  .poster {
    position: absolute; left: 78px; top: 48px;
    width: 782px; height: 1107px;
    background: linear-gradient(160deg, var(--bg-lavender) 0%, #e4bcee 45%, var(--bg-lavender-deep) 100%);
    box-shadow: 0 8px 40px rgba(0,0,0,0.28);
    overflow: hidden;
  }
  .bubble-field {
    position: absolute; inset: 0;
    background: radial-gradient(ellipse at 20% 30%, rgba(255,255,255,0.18), transparent 60%),
                radial-gradient(ellipse at 90% 80%, rgba(190,110,215,0.25), transparent 55%);
  }

  .brand-band {
    position: absolute; left: 0; top: 0; width: 100%; height: 76px;
    background: linear-gradient(to right, var(--brand-purple) 0 238px, var(--brand-blue) 238px);
  }
  .brand-name {
    position: absolute; left: 22px; top: 34px;
    color: #ffffff; font-weight: 800; font-size: 30px; letter-spacing: -0.5px;
    line-height: 1;
  }
  .brand-mark {
    position: absolute; left: 380px; top: 32px; width: 34px; height: 34px;
    background: var(--brand-orange);
  }

  .headline-bar {
    position: absolute; left: 60px; top: 76px; width: 659px; height: 89px;
    background: var(--brand-purple);
    border-radius: 0 0 11px 11px;
  }
  .headline {
    position: absolute; right: 14px; top: 30px;
    color: #ffffff; font-weight: 700; font-size: 42px; line-height: 1;
  }

  .content-panel {
    position: absolute; left: 56px; top: 414px; width: 672px; height: 648px;
    background: var(--panel-white);
    border: 7px solid var(--brand-purple);
    border-radius: 18px;
  }
  .content-copy {
    position: absolute; left: 25px; top: 105px; width: 605px;
    color: var(--text-purple); font-weight: 700; font-size: 21px; line-height: 28.6px;
  }
  .content-copy p + p { margin-top: 28px; }

  .feature-image {
    position: absolute; left: 220px; top: 205px; width: 540px; height: 255px;
    border: 4px solid var(--brand-purple); border-radius: 14px;
    background: linear-gradient(180deg, #dcecf2 0%, #eed6c8 40%, #f2cdb8 70%, #e8bba4 100%);
    box-shadow: 0 16px 30px rgba(80,120,140,0.35);
  }

  .footer-band {
    position: absolute; left: 0; bottom: 0; width: 100%; height: 19px;
    background: linear-gradient(to right,
      var(--brand-blue) 0 542px,
      var(--brand-orange) 542px 613px,
      var(--brand-purple) 613px);
  }
</style>
</head>
<body>
<div class="canvas">
  <div class="poster">
    <div class="bubble-field" role="img" aria-label="Soft bubble pattern background in lavender tones"></div>

    <header class="brand-band">
      <span class="brand-name">Tallowbrook Wellness</span>
      <span class="brand-mark"></span>
    </header>

    <div class="headline-bar">
      <h1 class="headline">Header text space</h1>
    </div>

    <section class="content-panel">
      <div class="content-copy">
        <p>Welcome to Tallowbrook Wellness. Our goal is to achieve the best possible health outcome for our patients. Our unique combination of therapies, structural correction and individualised exercise programs is what sets us apart.</p>
        <p>At anytime, if you have a health condition, even if you feel it is not something we could help you with, contact us and we will find the right solution for you. We are here for the health of our community"</p>
      </div>
    </section>

    <div class="feature-image" role="img" aria-label="Photo placeholder: a relaxed woman lying down receiving a shoulder treatment"></div>

    <footer class="footer-band"></footer>
  </div>
</div>
</body>
</html>
```